20 year old business card needs re-design

We need to redesign our corporate business card look. We need something that appears more modern, eye catchy but professional.

Target Market(s)

manufacturing industry

Industry/Entity Type

Manufacturer

Contact Information for Business Card

One side can have the logo. Other side can have contact information.

Font styles to use
Serif

Colors
3277b5
33b8a4
ffffff

Requirements
Must have
• Eye catchy - need to standout from the crowd. company logo cannot change. Full name, job title, phone number and email address.
Should not have
• Fax, business address is not necessary.

```html
<!DOCTYPE html>
<html lang="en">
<head>
<meta charset="utf-8">
<title>Norvale Industrial – Business Card</title>
<link href="https://fonts.googleapis.com/css2?family=Montserrat:wght@400;500;700&display=swap" rel="stylesheet">
<style>
  :root {
    --bg: #2a2a2b;
    --card: #1b1b1d;
    --card-edge: #232325;
    --blue: #3277b5;
    --teal: #33b8a4;
    --white: #ffffff;
    --silver: #6f6f74;
    --muted: #bfc3c8;
  }
  html, body {
    margin: 0;
    width: 1200px;
    height: 930px;
    overflow: hidden;
    background: var(--bg);
    font-family: "Montserrat", Arial, sans-serif;
  }
  .stage {
    position: relative;
    width: 1200px;
    height: 930px;
  }
  .card {
    position: absolute;
    left: 250px;
    width: 700px;
    height: 400px;
    border-radius: 18px;
    background: linear-gradient(160deg, var(--card-edge), var(--card));
    overflow: hidden;
    box-shadow: 0 18px 40px rgba(0,0,0,.45);
  }
  .card::after {
    content: "";
    position: absolute;
    left: 0; right: 0; bottom: 0;
    height: 9px;
    background: var(--blue);
  }
  .card--front { top: 45px; }
  .card--back  { top: 485px; }

  .wordmark {
    display: flex;
    align-items: center;
    gap: 14px;
    font-weight: 700;
    letter-spacing: 1px;
  }
  .wordmark__square {
    width: 22px;
    height: 22px;
    flex: none;
  }
  .card--front .wordmark {
    position: absolute;
    top: 140px;
    left: 0; right: 0;
    justify-content: center;
    font-size: 50px;
    color: var(--silver);
  }
  .card--front .wordmark__square { background: var(--silver); }
  .site-line {
    position: absolute;
    left: 0; right: 0;
    bottom: 70px;
    margin: 0;
    text-align: center;
    color: var(--muted);
    font-size: 16px;
    letter-spacing: 2px;
  }

  .card--back .wordmark {
    position: absolute;
    top: 150px;
    left: 50px;
    width: 310px;
    font-size: 34px;
    line-height: 1.1;
    color: var(--white);
  }
  .card--back .wordmark__square { background: var(--blue); width: 18px; height: 18px; }
  .divider {
    position: absolute;
    left: 385px;
    top: 95px;
    width: 1px;
    height: 190px;
    background: linear-gradient(var(--blue), var(--teal));
  }
  .contact {
    position: absolute;
    left: 415px;
    top: 100px;
    color: var(--white);
  }
  .contact__name {
    margin: 0;
    color: var(--blue);
    font-size: 26px;
    font-weight: 500;
    letter-spacing: .5px;
  }
  .contact__title {
    margin: 4px 0 26px;
    font-size: 17px;
  }
  .contact__list {
    list-style: none;
    margin: 0;
    padding: 0;
    font-size: 15px;
  }
  .contact__list li {
    display: flex;
    align-items: center;
    gap: 12px;
    margin-bottom: 10px;
  }
  .contact__list svg { width: 16px; height: 16px; flex: none; }
</style>
</head>
<body>
<main class="stage">

  <section class="card card--front" aria-label="Card front">
    <div class="wordmark"><span class="wordmark__square"></span>Norvale Industrial</div>
    <p class="site-line">norvaleindustrial.com</p>
  </section>

  <section class="card card--back" aria-label="Card back">
    <div class="wordmark"><span class="wordmark__square"></span><span>Norvale<br>Industrial</span></div>
    <div class="divider"></div>
    <div class="contact">
      <h1 class="contact__name">REN CALLOWAY</h1>
      <p class="contact__title">Sr. Project Manager</p>
      <ul class="contact__list">
        <li>
          <svg viewBox="0 0 16 16" aria-hidden="true"><rect x="4" y="1" width="8" height="14" rx="1.5" fill="none" stroke="#3277b5" stroke-width="1.6"/></svg>
          555-014-2200 ext 48
        </li>
        <li>
          <svg viewBox="0 0 16 16" aria-hidden="true"><rect x="1" y="3" width="14" height="10" rx="1" fill="#3277b5"/><path d="M1.5 4 8 9l6.5-5" fill="none" stroke="#1b1b1d" stroke-width="1.4"/></svg>
          ren@norvaleindustrial.com
        </li>
        <li>
          <svg viewBox="0 0 16 16" aria-hidden="true"><circle cx="6.5" cy="6.5" r="4.5" fill="none" stroke="#3277b5" stroke-width="2"/><path d="M10 10l4.5 4.5" stroke="#3277b5" stroke-width="2.2" stroke-linecap="round"/></svg>
          NorvaleIndustrial.com
        </li>
      </ul>
    </div>
  </section>

</main>
</body>
</html>
```